CrestHornSupply.com

I need a new webdesign for a company in the San Jose/SF Bay area that showcases the financial benefits of buying used band instruments for junior high students.This would be opposed to the current and costly option of renting cheap quality instruments from the 2 or 3 local music stores that charge a monthly fee that over the years charges the buyer 3 or 4x over..
Instruments: focus in on Alto Sax, Trumpet, Flute, Clarinet, Trombone, Tenor Sax, Baritone
Target middle schools are Larkfield Middle School and Maple Middle School in San Jose, CA. Both have award winning band programs.
Files attached may or may not be important.
Tabs Needed and funtional
Contact
Shopping Cart
Select Instrument
Checkout
Add to Cart, etc.
Instuments
quantity, etc.
trade in your instrument/sell your instrument
ability to add or take away new instruments for sale. including pictures
Additional questions or info, feel free to ask
Updates
Hi Designers,
Project Deadline Extended
Reason: In the next week you will be receiving specific content that will be required to be had on the website.
New desigins are still welcome. Please continue to contact me if you have questions about your individual designs.
Thanks!
Crest Horn

```html
<!DOCTYPE html>
<html lang="en">
<head>
<meta charset="utf-8">
<title>Crest Horn Instruments</title>
<link href="https://fonts.googleapis.com/css2?family=Signika:wght@400;600;700&family=Open+Sans:wght@400;600&family=Noto+Serif:wght@400&display=swap" rel="stylesheet">
<style>
:root{
  --green:#56a628;
  --green-dark:#4a9421;
  --red:#c4121a;
  --red-deep:#a80d14;
  --grey-btn:#6d6d6d;
  --ink:#333;
  --muted:#666;
  --page:#f3f3f3;
  --line:#dcdcdc;
  --white:#fff;
}
*{box-sizing:border-box;margin:0;padding:0}
html,body{width:1036px;height:1200px;overflow:hidden}
body{background:var(--page);font-family:"Open Sans",sans-serif;color:var(--ink);position:relative}
.wrap{width:845px;margin:0 auto;position:relative}
.rainbow{height:3px;background:linear-gradient(90deg,#f7a8b8,#f9d38a,#f3ef9a,#a8e3a0,#8fd8e0,#a9c4f2,#f7a8b8)}
/* header */
.site-header{height:102px}
.brand{position:absolute;left:0;top:18px;width:115px;height:78px;display:flex;align-items:center;justify-content:center;flex-direction:column;gap:6px}
.brand-mark{width:28px;height:28px;background:var(--green);border-radius:50%}
.brand-name{font-family:"Signika",sans-serif;font-weight:700;color:var(--red);font-size:16px;letter-spacing:.5px;white-space:nowrap}
.utility{position:absolute;right:0;top:16px;display:flex;gap:14px;font-family:"Noto Serif",serif;font-size:10px;color:var(--muted)}
.utility .item{display:flex;align-items:center;gap:6px;line-height:12px}
.utility svg{width:18px;height:18px}
.util-rule{position:absolute;right:0;top:52px;width:355px;border-top:1px solid var(--line)}
.tools{position:absolute;right:0;top:62px;display:flex;align-items:center;gap:10px;font-family:"Noto Serif",serif;font-size:10px;color:var(--muted)}
.account{display:flex;align-items:center;gap:5px}
.search{width:155px;height:23px;border:1px solid var(--line);background:var(--white);display:flex;align-items:center;justify-content:space-between;padding:0 6px 0 10px}
.cart{display:flex;height:23px}
.cart-icon{width:30px;background:var(--red);display:flex;align-items:center;justify-content:center}
.cart-total{background:#bfe8a2;color:#2d5a13;padding:0 5px;display:flex;align-items:center;font-size:11px}
/* nav */
.main-nav{background:var(--green);height:29px}
.main-nav ul{list-style:none;display:flex;height:29px;align-items:center}
.main-nav li{font-family:"Signika",sans-serif;font-weight:600;font-size:12.5px;color:var(--white);padding:0 10px;border-left:1px solid rgba(255,255,255,.35);line-height:12px}
.main-nav li:first-child{padding-left:0;border-left:0}
/* hero */
.hero{height:303px;position:relative;background:linear-gradient(100deg,#2a2420 0%,#9a6b3c 25%,#c79a5e 45%,#8d6a52 65%,#3d4a7a 85%,#6b4a8a 100%)}
.hero-card{position:absolute;left:95px;top:83px;width:295px;height:133px;background:rgba(240,240,240,.92);padding:14px 14px}
.hero-card h1{font-family:"Signika",sans-serif;font-weight:600;font-size:28px;color:#111;line-height:28px}
.hero-card p{font-size:12px;line-height:17px;color:#444;margin-top:8px;width:245px}
.btn-details{display:inline-block;margin-top:9px;background:var(--red);color:var(--white);font-family:"Signika",sans-serif;font-size:14px;padding:7px 25px}
.dots{position:absolute;left:100px;top:271px;display:flex;gap:3px}
.dots span{width:9px;height:9px;border-radius:50%;background:#ccc}
.dots span:first-child{background:#2a4c9a}
/* features */
.features{background:var(--red);height:83px}
.features .wrap{display:flex;height:83px;align-items:center}
.feature{display:flex;align-items:center;gap:14px;width:295px}
.feature .badge{width:55px;height:55px;border-radius:50%;background:var(--white);display:flex;align-items:center;justify-content:center;flex:none}
.feature h3{font-family:"Signika",sans-serif;font-weight:600;font-size:15.5px;color:var(--white)}
.feature p{font-size:10px;line-height:16.5px;color:#f4d6d6;margin-top:2px}
/* sections */
.section-head{display:flex;justify-content:space-between;align-items:center;height:46px}
.section-head h2{font-family:"Signika",sans-serif;font-weight:600;font-size:16px;color:#444}
.arrows{display:flex;gap:4px}
.products-grid{display:flex;gap:14px}
.product{width:201px;height:217px;background:var(--white);border:1px solid var(--line);padding:0 14px}
.product.active{border:2px solid var(--green)}
.product .shot{height:148px;margin:0 -6px;display:flex;align-items:center;justify-content:center}
.product .shot div{width:140px;height:90px;border-radius:6px}
.product .row{display:flex;justify-content:space-between;font-size:12px}
.product .name{font-family:"Signika",sans-serif;font-weight:600;color:#444}
.product .price{font-family:"Noto Serif",serif;color:var(--red)}
.product .actions{display:flex;justify-content:space-between;margin-top:14px}
.btn{font-family:"Signika",sans-serif;font-size:11px;color:var(--white);width:79px;height:24px;display:flex;align-items:center;justify-content:center}
.btn.view{background:var(--green)}
.btn.cart-add{background:var(--grey-btn)}
.testimonials{display:flex;gap:19px}
.testimonial{width:413px}
.quote{position:relative;background:var(--white);border:1px solid var(--line);height:127px;padding:30px 10px 0 25px;font-family:"Noto Serif",serif;font-size:11.2px;line-height:20px;color:#555}
.quote .mark{position:absolute;left:8px;top:8px;font-size:70px;line-height:70px;color:#ddd;font-family:"Noto Serif",serif}
.quote p{position:relative}
.quote:after{content:"";position:absolute;left:28px;bottom:-9px;width:14px;height:14px;background:var(--white);border-right:1px solid var(--line);border-bottom:1px solid var(--line);transform:rotate(45deg)}
.author{display:flex;align-items:center;gap:8px;margin-top:8px;font-family:"Noto Serif",serif;font-size:11.5px;color:#888}
.avatar{width:48px;height:48px;border-radius:50%;background:var(--white);border:1px solid var(--line);display:flex;align-items:center;justify-content:center}
/* footer */
.site-footer{position:absolute;left:0;top:1021px;width:1036px}
.footer-main{background:var(--red);height:120px}
.footer-main .wrap{display:flex;padding-top:14px}
.fcol h4{font-family:"Signika",sans-serif;font-weight:600;font-size:11.5px;color:var(--white);margin-bottom:8px}
.fcol ul{list-style:none;font-size:10px;color:#f3c4c4;line-height:17.5px}
.split{display:flex;gap:45px}
.field{width:138px;height:20px;background:var(--white);font-size:7px;color:#777;padding:6px 6px;margin-bottom:6px}
.subscribe{margin-left:58px;width:80px;height:19px;background:var(--red-deep);color:var(--white);font-family:"Noto Serif",serif;font-size:10.5px;display:flex;align-items:center;justify-content:center}
.social{display:flex;align-items:center;gap:10px;font-size:10.5px;color:#f3c4c4;margin-bottom:8px}
.social .dot{width:27px;height:27px;border-radius:50%;background:var(--white)}
.footer-bottom{background:var(--red-deep);height:59px}
.footer-bottom .wrap{display:flex;align-items:center;height:59px;font-size:10px;color:#f3c4c4;line-height:17px}
.pay-box{width:208px;height:38px;background:var(--white);border:2px solid #ddd;display:flex;align-items:center;padding:0 5px;gap:3px}
.pay-box span{width:20px;height:14px;background:#c9c9c9}
.pay-box .wallet{margin-left:14px;font-family:"Open Sans",sans-serif;font-weight:600;font-size:13px;color:#2a4c9a}
</style>
</head>
<body>
<div class="rainbow"></div>
<header class="site-header">
  <div class="wrap">
    <a class="brand"><span class="brand-mark"></span><span class="brand-name">CREST HORN</span></a>
    <div class="utility">
      <div class="item"><svg viewBox="0 0 18 18"><circle cx="9" cy="9" r="9" fill="#777"/><rect x="4" y="6" width="7" height="5" fill="#fff"/><rect x="11" y="8" width="3" height="3" fill="#fff"/></svg>Shipping</div>
      <div class="item"><svg viewBox="0 0 18 18"><circle cx="9" cy="9" r="9" fill="#777"/><path d="M5 8c0-2 8-2 8 0v1h-2V8H7v1H5z M6 10h6l1 3H5z" fill="#fff"/></svg><span>Customer Hotline<br>1-408-555-0172</span></div>
      <div class="item"><svg viewBox="0 0 18 18"><circle cx="9" cy="9" r="9" fill="#777"/><path d="M9 4a3 3 0 0 1 3 3c0 2-3 6-3 6s-3-4-3-6a3 3 0 0 1 3-3z" fill="#fff"/><circle cx="9" cy="7" r="1" fill="#777"/></svg><span>Store<br>Locations</span></div>
    </div>
    <div class="util-rule"></div>
    <div class="tools">
      <div class="account"><svg width="16" height="16" viewBox="0 0 16 16"><circle cx="8" cy="8" r="7" fill="none" stroke="#888"/><circle cx="8" cy="6" r="2.5" fill="none" stroke="#888"/><path d="M3.5 12.5c1-2.5 8-2.5 9 0" fill="none" stroke="#888"/></svg>My Account</div>
      <div class="search"><span>Search</span><svg width="13" height="13" viewBox="0 0 13 13"><circle cx="5.5" cy="5.5" r="4.3" fill="none" stroke="#555" stroke-width="1.5"/><path d="M8.6 8.6 12 12" stroke="#555" stroke-width="1.8"/></svg></div>
      <div class="cart"><div class="cart-icon"><svg width="18" height="16" viewBox="0 0 18 16"><path d="M1 2h3l2 8h9l2-6H5" fill="none" stroke="#fff" stroke-width="1.6"/><circle cx="7" cy="13" r="1.5" fill="#fff"/><circle cx="14" cy="13" r="1.5" fill="#fff"/></svg></div><div class="cart-total">0 items: $0.00</div></div>
    </div>
  </div>
</header>
<nav class="main-nav"><div class="wrap"><ul>
  <li>HOME</li><li>ABOUT US</li><li>PRODUCTS</li><li>SALE</li><li>SELECT INSTRUMENT</li><li>INSTUMENTS</li><li>QUANTITY</li><li>CONTACT US</li>
</ul></div></nav>
<section class="hero" role="img" aria-label="Photo of young students playing a trumpet in a school gym">
  <div class="hero-card">
    <h1>BAND INSTRUMENTS</h1>
    <p>Lorem Ipsum is simply dummy text of the printing and typesetting industry</p>
    <span class="btn-details">DETAILS</span>
  </div>
  <div class="dots"><span></span><span></span><span></span></div>
</section>
<section class="features"><div class="wrap">
  <div class="feature"><div class="badge"><svg width="26" height="26" viewBox="0 0 26 26"><circle cx="13" cy="13" r="11" fill="none" stroke="#c4121a" stroke-width="2"/><path d="M8 13l4 4 7-9" fill="none" stroke="#c4121a" stroke-width="3"/></svg></div><div><h3>CUSTOMER SATISFACTION</h3><p>Lorem Ipsum is simply dummy text of the<br>printing and typesetting industry</p></div></div>
  <div class="feature"><div class="badge"><svg width="28" height="28" viewBox="0 0 28 28"><path d="M15 3h10v10L13 25 3 15z" fill="#c4121a"/><circle cx="20" cy="8" r="2.2" fill="#fff"/></svg></div><div><h3>PRODUCTS</h3><p>Lorem Ipsum is simply dummy text of the<br>printing and typesetting industry</p></div></div>
  <div class="feature"><div class="badge"><svg width="30" height="26" viewBox="0 0 30 26"><ellipse cx="15" cy="11" rx="12" ry="8.5" fill="none" stroke="#c4121a" stroke-width="2"/><path d="M8 18l-3 6 8-4" fill="none" stroke="#c4121a" stroke-width="2"/></svg></div><div><h3>FEEDBACK</h3><p>Lorem Ipsum is simply dummy text of the<br>printing and typesetting industry</p></div></div>
</div></section>
<main class="wrap">
  <div class="section-head"><h2>PRODUCTS</h2><div class="arrows"><svg width="11" height="16"><path d="M9 1 2 8l7 7" fill="none" stroke="#999" stroke-width="1.5"/></svg><svg width="11" height="16"><path d="M2 1l7 7-7 7" fill="none" stroke="#999" stroke-width="1.5"/></svg></div></div>
  <div class="products-grid">
    <article class="product active"><div class="shot"><div role="img" aria-label="Product photo of a red instrument" style="background:linear-gradient(160deg,#fbe3e3,#f2a2a2)"></div></div><div class="row"><span class="name">ALTO SAX</span><span class="price">$20,00</span></div><div class="actions"><span class="btn view">View Detail</span><span class="btn cart-add">Add to Cart</span></div></article>
    <article class="product"><div class="shot"><div role="img" aria-label="Product photo of a brass trumpet" style="background:linear-gradient(160deg,#f7f0d4,#dcc77a)"></div></div><div class="row"><span class="name">TRUMPET</span><span class="price">$20,00</span></div><div class="actions"><span class="btn view">View Detail</span><span class="btn cart-add">Add to Cart</span></div></article>
    <article class="product"><div class="shot"><div role="img" aria-label="Product photo of a flute" style="background:linear-gradient(160deg,#fde8d6,#f2b27a)"></div></div><div class="row"><span class="name">FLUTE</span><span class="price">$20,00</span></div><div class="actions"><span class="btn view">View Detail</span><span class="btn cart-add">Add to Cart</span></div></article>
    <article class="product"><div class="shot"><div role="img" aria-label="Product photo of a black clarinet" style="background:linear-gradient(160deg,#eeeeee,#b9b9b9)"></div></div><div class="row"><span class="name">CLARINET</span><span class="price">$20,00</span></div><div class="actions"><span class="btn view">View Detail</span><span class="btn cart-add">Add to Cart</span></div></article>
  </div>
  <div class="section-head" style="margin-top:6px;height:42px"><h2>CUSTOMER TESTIMONIALS</h2><div class="arrows"><svg width="11" height="16"><path d="M9 1 2 8l7 7" fill="none" stroke="#999" stroke-width="1.5"/></svg><svg width="11" height="16"><path d="M2 1l7 7-7 7" fill="none" stroke="#999" stroke-width="1.5"/></svg></div></div>
  <div class="testimonials">
    <div class="testimonial"><div class="quote" style="padding-top:25px"><span class="mark">“</span><p>Lorem Ipsum is simply dummy text of the printing and &nbsp;typesetting industry. Lorem Ipsum has been the industry's standard dummy text ever since the 1500s, when an unknown printer took a galley of type and scrambled it to make a type specimen book.</p></div><div class="author"><div class="avatar"><svg width="24" height="26" viewBox="0 0 24 26"><circle cx="12" cy="8" r="6" fill="#bbb"/><path d="M1 26c1-8 21-8 22 0z" fill="#bbb"/></svg></div>Sam Rivera</div></div>
    <div class="testimonial"><div class="quote"><span class="mark">“</span><p>Lorem Ipsum is simply dummy text of the printing and &nbsp;typesetting industry. Lorem Ipsum has been the industry's standard dummy text ever since the 1500s, when an unknown printer took a galley of type and scrambled it to make a type specimen book.</p></div><div class="author"><div class="avatar"><svg width="24" height="26" viewBox="0 0 24 26"><circle cx="12" cy="8" r="6" fill="#bbb"/><path d="M1 26c1-8 21-8 22 0z" fill="#bbb"/></svg></div>Sam Rivera</div></div>
  </div>
</main>
<footer class="site-footer">
  <div class="footer-main"><div class="wrap">
    <div class="fcol" style="width:224px"><h4>VIEW ALL OF OUR PRODUCTS</h4><div class="split"><ul><li>Alto Sax</li><li>Trumpet</li><li>Flute</li><li>Clarinet</li></ul><ul style="margin-left:40px"><li>Trombone</li><li>Tenor Sax</li><li>Baritone</li></ul></div></div>
    <div class="fcol" style="width:154px"><h4>YOUR ACCOUNT</h4><ul><li>Sign In</li><li>Your Basket (0)</li><li>Checkout</li><li>Register</li></ul></div>
    <div class="fcol" style="width:162px"><h4>LET US HELP</h4><ul><li>Contact Us</li><li>Terms &amp; Conditions</li><li>Returns &amp; Shipping</li><li>About Us</li></ul></div>
    <div class="fcol" style="width:198px"><h4>JOIN OUR MAILING LIST</h4><div class="field">Name</div><div class="field">Email Address</div><div class="subscribe">SUBSCRIBE</div></div>
    <div class="fcol"><h4>FOLLOW US</h4><div class="social" style="margin-top:10px"><span class="dot"></span>Friendbook</div><div class="social"><span class="dot"></span>Chirper</div></div>
  </div></div>
  <div class="footer-bottom"><div class="wrap">
    <div class="pay-box"><span></span><span></span><span></span><span></span><span></span><span class="wallet">WalletLink</span></div>
    <div style="margin-left:12px">We accept CardOne, NorthPay payments.<br>We also take payments from customers with a WalletLink account.</div>
    <div style="margin-left:auto;margin-top:17px">Copyright © 2014 CrestHorn. All Rights Reserved.</div>
  </div></div>
</footer>
</body>
</html>
```